Business Card Design

It's an investment advisory service for individuals with all there investment needs. Also financial consulting to businesses and governmental agencies on retirement plans etc. It's personalized not commoditized help. Should show strength, knowledge and money orientation.

Reason: Will be out of town setting up office.

Reason: waiting for the 2/3rds of group to vote

Reason: only half the votes are in, I'm calling and getting verbals, but at this time we are down to 2 designs.

Industry/Entity Type

Investment

Contact Information for Business Card

B. Rel K. Financial Consulting and Wealth Management, Berislav Mike Holcek, 5172 Pasadena Loma Verde, San Diego, CA 94417-6381, Registered Investment Advisor

Requirements
Nice to have
• Something money oriented

```html
<!DOCTYPE html>
<html lang="en">
<head>
<meta charset="utf-8">
<title>B. Rel K. Business Card</title>
<link rel="stylesheet" href="https://fonts.googleapis.com/css2?family=Crimson+Text:wght@400;600;700&display=swap">
<style>
  :root {
    --stage: #000000;
    --green-deep: #0b5a2c;
    --green-mid: #3f8a5c;
    --green-pale: #cfe3da;
    --mist: #e9f1ee;
    --logo-box: #0f4a2a;
    --logo-text: #f2f5f0;
    --tagline: #7fa58d;
    --name-ink: #0d3a1f;
    --contact-ink: #ffffff;
    --border-strip: #9fc0ac;
    --beast: #5c7f68;
  }
  * { box-sizing: border-box; margin: 0; padding: 0; }
  html, body { width: 1200px; height: 1000px; overflow: hidden; background: var(--stage); }
  body { position: relative; font-family: "Crimson Text", Georgia, serif; }

  .card {
    position: absolute; left: 302px; width: 656px; height: 373px; overflow: hidden;
  }
  .card--front {
    top: 120px;
    background: radial-gradient(ellipse 75% 45% at 50% 20%, #ffffff 0%, var(--mist) 30%, rgba(233,241,238,0) 70%),
                linear-gradient(to bottom, var(--green-pale) 0%, #c9ddd2 35%, var(--green-mid) 70%, var(--green-deep) 100%);
  }
  .card--back {
    top: 526px; height: 374px;
    background: linear-gradient(to bottom, var(--green-pale) 0%, #a8c4b2 40%, #6a9a7c 70%, var(--green-deep) 100%);
  }
  .edge-strip {
    position: absolute; top: 0; bottom: 0; width: 28px;
    background: linear-gradient(to bottom, #b9d2c3, #3f7a55);
    opacity: .55;
  }
  .edge-strip--left { left: 0; }
  .edge-strip--right { right: 0; }

  .logo-box {
    position: absolute; left: 230px; top: 78px; width: 192px; height: 180px;
    background: var(--logo-box);
    display: flex; flex-direction: column; align-items: center; justify-content: center;
    padding: 0 18px; text-align: center;
    color: var(--logo-text); font-weight: 400;
  }
  .logo-box .firm-mark { font-size: 40px; line-height: 1; }
  .logo-box .firm-line { font-size: 11px; letter-spacing: .04em; line-height: 1.3; margin-top: 14px; text-transform: uppercase; }

  .tagline {
    position: absolute; left: 0; right: 0; top: 296px; text-align: center;
    font-size: 17px; letter-spacing: .12em; color: var(--tagline);
  }

  .holder-name {
    position: absolute; left: 62px; top: 44px;
    font-size: 28px; font-weight: 700; color: var(--name-ink);
  }
  .credentials {
    position: absolute; left: 62px; top: 82px;
    font-size: 17px; color: var(--name-ink);
  }
  .credentials sup { font-size: 10px; }

  .art-bear, .art-bull {
    position: absolute;
    background: linear-gradient(to bottom, rgba(92,127,104,.75), rgba(70,105,82,.7));
    border-radius: 40% 45% 20% 20%;
  }
  .art-bear { left: 50px; top: 122px; width: 330px; height: 214px; }
  .art-bull { left: 418px; top: 52px; width: 172px; height: 206px; border-radius: 35% 35% 15% 15%; }

  .contact {
    position: absolute; right: 50px; top: 290px; text-align: right;
    font-size: 19px; line-height: 1.35; color: var(--contact-ink);
  }
  .contact svg { width: 15px; height: 15px; vertical-align: -1px; margin-right: 4px; }
</style>
</head>
<body>
  <section class="card card--front">
    <div class="edge-strip edge-strip--left" role="img" aria-label="Engraved banknote-style ornamental border"></div>
    <div class="edge-strip edge-strip--right" role="img" aria-label="Engraved banknote-style ornamental border"></div>
    <div class="logo-box">
      <div class="firm-mark">B. Rel K.</div>
      <div class="firm-line">Financial Consulting &amp; Wealth Management</div>
    </div>
    <p class="tagline">REGISTERED INVESTMENT ADVISOR</p>
  </section>

  <section class="card card--back">
    <div class="edge-strip edge-strip--left" role="img" aria-label="Engraved banknote-style ornamental border"></div>
    <div class="edge-strip edge-strip--right" role="img" aria-label="Engraved banknote-style ornamental border"></div>
    <div class="art-bear" role="img" aria-label="Engraved line-art silhouette of a bear"></div>
    <div class="art-bull" role="img" aria-label="Engraved line-art silhouette of a bull"></div>
    <h1 class="holder-name">Berislav “Mike” Holcek</h1>
    <p class="credentials">MBA, RP<sup>©</sup>, CRC<sup>©</sup></p>
    <div class="contact">
      <p><svg viewBox="0 0 16 16" aria-hidden="true"><circle cx="8" cy="8" r="7" fill="none" stroke="#fff" stroke-width="1"/><path d="M5.5 4.5l1.5 0 .6 2-1 .8c.5 1.1 1.2 1.8 2.2 2.2l.8-1 2 .6v1.5c0 .5-.5.9-1 .9C7.5 11.3 4.7 8.5 4.6 5.5c0-.5.4-1 .9-1z" fill="#fff"/></svg>858-555-0147 / 775-555-0193</p>
      <p>mike.holcek@mailbox.net</p>
    </div>
  </section>
</body>
</html>
```